Harbourline Physiotherapy business card design

We need a fresh, new business card design for our physiotherapy clinic Harbourline Physiotherapy

Will attach logo soon we had logo designed from our last project

Industry/Entity Type

Physical Therapy

Contact Information for Business Card

On front
Needs our logo, contact details:
58 Wexley Lane St Clair NSW 2759
Ph/f: 02 9481 2057
info@harbourlinephysio.example.com.au

Requirements
Must have
• On the back of the card needs to have area to write down follow up appointments
• On front
• Needs our logo
• The colours have to be the colours in our logo which are: sky blue, black and white
• Font to be same as our logo please
• We want the card to look simple, not too cluttered but to the point
Should not have
• We don't need any extra pictures other than our logo

```html
<!DOCTYPE html>
<html lang="en">
<head>
<meta charset="utf-8">
<title>Harbourline Physiotherapy – Business Card</title>
<link href="https://fonts.googleapis.com/css2?family=Open+Sans:wght@400;600;700&display=swap" rel="stylesheet">
<style>
  :root{
    --bg:#e9e5df;
    --card:#ffffff;
    --navy:#2f3c8e;
    --sky:#2a86d6;
    --sky-light:#4aa8ec;
    --sky-deep:#1f6fc4;
    --band-dark:#2b2f3a;
    --band-mid:#8a8f98;
    --band-pale:#dfe6f2;
    --ink:#333333;
    --grey:#5a5d63;
    --dot:#4b8fd6;
  }
  *{margin:0;padding:0;box-sizing:border-box}
  html,body{width:1200px;height:843px;overflow:hidden;background:var(--bg);font-family:"Open Sans",Arial,sans-serif}
  .canvas{position:relative;width:1200px;height:843px}
  .card{position:absolute;width:580px;height:352px;background:var(--card);box-shadow:0 6px 18px rgba(0,0,0,.18);overflow:hidden}

  /* back: appointment card */
  .card--back{left:50px;top:60px}
  .appt-title{position:absolute;right:60px;top:24px;color:var(--sky);font-weight:700;font-size:19px}
  .field{position:absolute;color:var(--sky);font-size:14px;display:flex;align-items:flex-end;gap:6px;white-space:nowrap}
  .field .rule{flex:1;border-bottom:2px dotted var(--dot);height:1px;margin-bottom:4px}
  .ampm{position:absolute;right:38px;top:86px;font-size:10px;color:var(--sky)}
  .days{position:absolute;left:50px;right:30px;top:192px;display:flex;justify-content:space-between;color:var(--sky);font-size:13px}
  .day{display:flex;align-items:center;gap:6px}
  .box{width:13px;height:13px;border:1px solid var(--grey);background:#fff}
  .note-rule{position:absolute;left:120px;right:40px;top:272px;border-bottom:2px dotted var(--dot)}
  .notice{position:absolute;left:0;right:0;text-align:center;color:var(--grey);font-size:10.5px;white-space:nowrap}
  .notice--lead{top:220px;left:auto;right:40px;text-align:right}
  .notice--close{top:300px}

  /* front */
  .card--front{left:570px;top:420px}
  .brand{position:absolute;right:40px;top:56px;display:flex;align-items:center;gap:12px}
  .brand-dot{width:40px;height:40px;border-radius:50%;background:var(--sky)}
  .brand-name{color:var(--navy);font-weight:700;font-size:24px;line-height:1.05}
  .person{position:absolute;left:48px;top:100px}
  .person-name{color:var(--navy);font-weight:600;font-size:21px}
  .person-role{color:var(--ink);font-size:14px}
  .divider{position:absolute;left:150px;right:42px;top:156px;border-top:1px solid var(--navy)}
  .contacts{position:absolute;left:48px;top:160px;list-style:none;font-size:13.5px;color:var(--ink)}
  .contacts li{display:flex;align-items:center;gap:8px;height:21px;white-space:nowrap}
  .contacts svg{width:13px;height:13px;fill:var(--navy)}
  .address{position:absolute;right:42px;top:214px;text-align:right;color:var(--ink);font-size:15px;line-height:1.35}
  .footer-band{position:absolute;left:0;bottom:0;width:580px;height:100px}
  .web{position:absolute;right:28px;bottom:26px;color:#fff;font-size:15px;white-space:nowrap}
</style>
</head>
<body>
<div class="canvas">

  <section class="card card--back" aria-label="Appointment card, back">
    <h2 class="appt-title">Next Appointment</h2>
    <div class="field" style="left:40px;right:250px;top:110px"><span>Name :</span><span class="rule"></span></div>
    <div class="field" style="left:355px;right:30px;top:98px"><span>Time :</span><span class="rule"></span></div>
    <span class="ampm">AM/PM</span>
    <div class="field" style="left:40px;right:30px;top:148px"><span>Date :</span><span class="rule"></span></div>
    <div class="days">
      <span class="day">Sun <i class="box"></i></span>
      <span class="day">Mon <i class="box"></i></span>
      <span class="day">Tue <i class="box"></i></span>
      <span class="day">Wed <i class="box"></i></span>
      <span class="day">Thu <i class="box"></i></span>
      <span class="day">Fri <i class="box"></i></span>
      <span class="day">Sat <i class="box"></i></span>
    </div>
    <p class="notice notice--lead">If you are unable to attend your appointment or</p>
    <div class="field" style="left:55px;right:40px;top:238px"><span>Note :</span><span class="rule"></span></div>
    <div class="note-rule"></div>
    <p class="notice notice--close">Please give me 24 hours notice to cancel.</p>
  </section>

  <section class="card card--front" aria-label="Business card, front">
    <div class="brand">
      <span class="brand-dot"></span>
      <span class="brand-name">Harbourline<br>Physiotherapy</span>
    </div>
    <div class="person">
      <p class="person-name">Daniel Hartley</p>
      <p class="person-role">CEO/Founder</p>
    </div>
    <div class="divider"></div>
    <ul class="contacts">
      <li><svg viewBox="0 0 16 16"><path d="M3 1l3 3-1.5 2c1 2 3 4 5 5l2-1.5 3 3-2 2C7 14 2 9 1 3z"/></svg>02 9481 2057</li>
      <li><svg viewBox="0 0 16 16"><rect x="4" y="1" width="8" height="5"/><rect x="1" y="6" width="14" height="7" rx="1"/><rect x="4" y="11" width="8" height="4" fill="#fff"/></svg>02 9481 2057</li>
      <li><svg viewBox="0 0 16 16"><path d="M1 3h14v10H1z"/><path d="M1 3l7 6 7-6" fill="none" stroke="#fff" stroke-width="1.3"/></svg>info@harbourlinephysio.example.com.au</li>
    </ul>
    <p class="address">58 Wexley Lane Fernmoor<br>NSW 2764</p>
    <svg class="footer-band" viewBox="0 0 580 100" aria-hidden="true">
      <defs>
        <linearGradient id="bandGrey" x1="0" x2="1">
          <stop offset="0" stop-color="var(--band-dark)"/><stop offset="1" stop-color="var(--band-mid)"/>
        </linearGradient>
        <linearGradient id="bandSky" x1="0" x2="1">
          <stop offset="0" stop-color="var(--sky-light)"/><stop offset="1" stop-color="var(--sky-deep)"/>
        </linearGradient>
      </defs>
      <path d="M0 8 H240 L255 20 H0 Z" fill="url(#bandGrey)"/>
      <path d="M0 20 H255 L270 34 Q275 38 285 38 H0 Z" fill="var(--band-pale)"/>
      <path d="M262 48 Q272 36 292 36 H580 V100 H240 Z" fill="url(#bandSky)"/>
      <rect x="0" y="88" width="580" height="12" fill="var(--navy)"/>
    </svg>
    <span class="web">harbourlinephysio.example.com.au</span>
  </section>

</div>
</body>
</html>
```